Redesign website for small print company

Vindurgata is a small printing company in Iceland mainly servicing Students, schools, etc. We are also doing all kind of other jobs, like business cards, book printing, brochure printing etc. We are also selling books online.
Our website is: www.vindurgata.is
What we are looking for is:
- Web Design (Uncoded - PSD layout only)
- Mobile friendly design, using our current color scheme: Red, green, yellow and light gray.
- Clean simple design
- Simple, light and easy to use.
- More menu Items/drop down
Industry/Entity Type
Digital Printing
Number of Pages Required
5+ page
Requirements
Must have
- Easy navigation
- Designed for mobile
- Current color scheme (see logo)
Nice to have
- Icon based products

```html
<!DOCTYPE html>
<html lang="en">
<head>
<meta charset="utf-8">
<title>Vindurgata</title>
<link href="https://fonts.googleapis.com/css2?family=Lato:wght@400;700;900&family=Roboto:wght@400;500;700&display=swap" rel="stylesheet">
<style>
:root{
  --red:#e3262b;
  --green:#0d5a2c;
  --yellow:#e7b812;
  --dark:#1f1f1f;
  --text:#333;
  --muted:#666;
  --light:#f3f3f3;
  --white:#fff;
}
*{box-sizing:border-box;margin:0;padding:0}
html,body{width:1200px;height:3327px;overflow:hidden;background:var(--white)}
body{font-family:'Roboto',sans-serif;color:var(--text)}
.page{position:relative;width:1200px;height:3327px;overflow:hidden}
.abs{position:absolute}

/* header */
.topline{left:0;top:0;width:1200px;height:4px;background:var(--red)}
.header{left:0;top:4px;width:1200px;height:96px;background:var(--white)}
.brand{left:98px;top:30px;display:flex;align-items:center;gap:12px;font-family:'Lato',sans-serif;font-weight:900;font-size:30px;color:var(--dark);letter-spacing:.5px}
.brand-square{width:38px;height:38px;background:var(--red)}
.nav{left:550px;top:42px;display:flex;gap:24px;font-family:'Roboto',sans-serif;font-weight:700;font-size:15px;color:var(--dark);text-transform:uppercase}
.nav .active{color:var(--dark)}
.icon-btn{top:33px;width:36px;height:36px;border-radius:50%;display:flex;align-items:center;justify-content:center}
.icon-search{left:1017px;border:2px solid #ddd;background:var(--white)}
.icon-cart{left:1063px;background:var(--green)}
.dropdown{left:670px;top:73px;width:180px;height:211px;background:var(--red);padding:22px 0 0 26px;z-index:5}
.dropdown li{list-style:none;color:var(--white);font-weight:700;font-size:15px;line-height:29px}
.dropdown li::before{content:"» ";}

/* hero */
.hero{left:0;top:100px;width:1200px;height:556px;background:linear-gradient(100deg,#c9a882 0%,#d8cfc4 35%,#aeb3b6 60%,#7b756d 100%)}
.hero-title{left:585px;top:180px;font-family:'Lato',sans-serif;font-weight:900;font-size:58px;color:var(--dark);letter-spacing:1px}
.hero-text{left:585px;top:266px;width:520px;font-weight:700;font-size:20px;line-height:30px;color:var(--dark)}
.btn{display:flex;align-items:center;justify-content:center;gap:8px;font-weight:700;font-size:16px;text-transform:uppercase;color:var(--white)}
.btn-green{background:var(--green)}
.btn-red{background:var(--red)}
.btn-yellow{background:var(--yellow);color:var(--dark)}
.hero-btn{left:585px;top:355px;width:174px;height:49px}

/* categories */
.cats{left:0;top:656px;width:1200px;height:147px;display:flex}
.cat{width:200px;height:147px;display:flex;flex-direction:column;align-items:center;justify-content:flex-end;padding-bottom:20px;gap:14px;color:var(--white);font-weight:700;font-size:17px;text-transform:uppercase}
.cat.red{background:var(--red)}.cat.green{background:var(--green)}.cat.yellow{background:var(--yellow)}

/* shared section */
.soft-bg{left:0;top:803px;width:1200px;height:1213px;background:linear-gradient(180deg,#f7f7f7 0%,#eeeeee 40%,#f6f6f6 100%)}
.ghost{font-family:'Lato',sans-serif;font-weight:900;font-size:76px;color:rgba(0,0,0,.06);white-space:nowrap;text-transform:uppercase}
.section-title{font-family:'Lato',sans-serif;font-weight:900;font-size:36px;color:var(--dark);text-transform:uppercase}
.center{left:0;width:1200px;text-align:center}
.lede{font-size:14px;line-height:26px;color:var(--muted)}

/* welcome */
.welcome-ghost{left:0;top:888px}
.welcome-title{left:98px;top:912px}
.welcome-text{left:98px;top:988px;width:480px;font-size:14px;line-height:24px;color:var(--muted)}
.welcome-text p{margin-bottom:16px}
.welcome-btn{left:98px;top:1184px;width:160px;height:48px}
.video{left:634px;top:925px;width:466px;height:304px;border:4px solid var(--white);box-shadow:0 2px 8px rgba(0,0,0,.2);background:linear-gradient(135deg,#6e8b83,#b9b0a3 50%,#4f5a57)}
.play{left:834px;top:1054px;width:66px;height:46px;border-radius:12px;background:var(--red)}
.divider{left:98px;top:1338px;width:1002px;height:1px;background:#d5d5d5}

/* latest */
.latest-ghost{top:1410px}
.latest-title{top:1434px}
.latest-lede{top:1498px}
.work{width:224px}
.work-img{width:224px;height:166px}
.work-cap{margin-top:22px;border-left:3px solid var(--red);padding-left:14px}
.work-cap h3{font-size:18px;font-weight:700;color:var(--dark)}
.work-cap p{font-size:13px;color:var(--muted);margin-top:8px}
.works-btn{left:495px;top:1865px;width:210px;height:49px}

/* how */
.how{left:0;top:2016px;width:1200px;height:335px;background:var(--green)}
.how-ghost{top:2058px;color:rgba(255,255,255,.1)}
.how-title{top:2082px;color:var(--white)}
.how-lede{top:2146px;color:var(--white)}
.how-lower{left:0;top:2351px;width:1200px;height:270px;background:linear-gradient(180deg,#f4f4f4,#ffffff)}
.step{width:204px;height:204px;border-radius:50%;background:var(--white);box-shadow:0 3px 10px rgba(0,0,0,.25);display:flex;flex-direction:column;align-items:center;justify-content:center;gap:12px;font-family:'Lato',sans-serif;font-weight:900;font-size:19px;color:var(--dark)}

/* books */
.books-ghost{top:2510px}
.books-title{top:2534px}
.book-cover{width:166px;height:217px;box-shadow:0 2px 6px rgba(0,0,0,.2)}
.book-info{width:270px}
.book-info h3{font-family:'Lato',sans-serif;font-weight:700;font-size:27px;color:var(--dark)}
.book-info .author{color:var(--red);font-size:15px;margin-top:6px}
.book-info p{font-size:13px;line-height:22px;color:var(--muted);margin-top:14px}
.buy{width:118px;height:37px;font-size:14px;margin-top:16px}

/* footer */
.foot-photo{left:0;top:2974px;width:400px;height:353px;background:linear-gradient(160deg,#5d8ac0,#2a4f82 50%,#18304e)}
.foot-mid{left:400px;top:2974px;width:400px;height:353px;background:#262626;color:var(--white);text-align:center}
.foot-map{left:800px;top:2974px;width:400px;height:353px;background:linear-gradient(135deg,#eae7df,#dcd9cf)}
.up{left:570px;top:2944px;width:60px;height:60px;border-radius:50%;background:var(--white);border:2px solid #ddd;display:flex;align-items:center;justify-content:center;z-index:3}
.foot-h{font-weight:700;font-size:16px;text-transform:uppercase;letter-spacing:.5px}
.email-field{left:57px;top:89px;width:286px;height:37px;border:1px solid #bbb;font-size:13px;text-align:left;padding:10px 10px}
.subscribe{left:135px;top:138px;width:130px;height:37px;font-size:15px}
.contact-line{display:flex;justify-content:center;align-items:center;gap:10px;font-size:15px}
.direction{left:18px;top:16px;width:134px;height:34px;font-size:13px;color:var(--dark)}
</style>
</head>
<body>
<div class="page">

  <div class="abs topline"></div>
  <header class="abs header"></header>
  <div class="abs brand"><span class="brand-square"></span>VINDURGATA</div>
  <nav class="abs nav">
    <span>Home</span><span class="active">Services ⌄</span><span>Submission of works</span><span>About us</span>
  </nav>
  <div class="abs icon-btn icon-search">
    <svg width="16" height="16" viewBox="0 0 16 16"><circle cx="6.5" cy="6.5" r="4.5" fill="none" stroke="#e3262b" stroke-width="2.2"/><line x1="10" y1="10" x2="14" y2="14" stroke="#e3262b" stroke-width="2.4"/></svg>
  </div>
  <div class="abs icon-btn icon-cart">
    <svg width="18" height="16" viewBox="0 0 18 16"><path d="M1 2h3l2 8h9l2-6H5" fill="none" stroke="#fff" stroke-width="2"/><circle cx="7" cy="13.5" r="1.5" fill="#fff"/><circle cx="14" cy="13.5" r="1.5" fill="#fff"/></svg>
  </div>
  <ul class="abs dropdown">
    <li>Essays</li><li>Business Cards</li><li>Pamphlets</li><li>Book Printing</li><li>Posters</li><li>Textbooks</li>
  </ul>

  <section class="abs hero" role="img" aria-label="Photo of smiling students on a campus holding notebooks"></section>
  <h1 class="abs hero-title">VINDURGATA</h1>
  <p class="abs hero-text">Nemo enim ipsam voluptatem quia voluptas aspernatur aut odit aut fugit sed quia magni dolores.</p>
  <a class="abs btn btn-green hero-btn">Read more
    <svg width="16" height="16" viewBox="0 0 16 16"><circle cx="8" cy="8" r="7" fill="#fff"/><path d="M6 4.5 9.5 8 6 11.5" fill="none" stroke="#0d5a2c" stroke-width="2"/></svg></a>

  <div class="abs cats">
    <div class="cat red"><svg width="56" height="64" viewBox="0 0 56 64" fill="none" stroke="#fff" stroke-width="2.5"><path d="M10 4h28l10 10v46H10z"/><path d="M38 4v10h10M18 26h20M18 34h20M18 42h14"/></svg>Essays</div>
    <div class="cat green"><svg width="70" height="64" viewBox="0 0 70 64" fill="none" stroke="#fff" stroke-width="2.5"><path d="M6 36 36 8l28 20-30 28z"/><path d="M14 36 36 16M22 42 44 22"/></svg>Business Cards</div>
    <div class="cat yellow"><svg width="72" height="64" viewBox="0 0 72 64" fill="none" stroke="#fff" stroke-width="2.5"><path d="M4 10l21 6 22-6 21 6v42l-21-6-22 6-21-6z"/><path d="M25 16v42M47 10v42"/></svg>Pamphlets</div>
    <div class="cat red"><svg width="66" height="64" viewBox="0 0 66 64" fill="none" stroke="#fff" stroke-width="2.5"><path d="M33 14C24 8 12 8 4 10v44c8-2 20-2 29 4 9-6 21-6 29-4V10c-8-2-20-2-29 4z"/><path d="M33 14v44M12 22h14M12 30h14M40 22h14M40 30h14"/></svg>Book Printing</div>
    <div class="cat green"><svg width="66" height="64" viewBox="0 0 66 64" fill="none" stroke="#fff" stroke-width="2.5"><rect x="6" y="6" width="54" height="40"/><path d="M33 46v12M20 58h26M18 18h12M36 18h12M18 30h30"/></svg>Posters</div>
    <div class="cat yellow"><svg width="60" height="64" viewBox="0 0 60 64" fill="none" stroke="#fff" stroke-width="2.5"><path d="M8 10h38v44H8zM46 54h6V14"/><rect x="30" y="4" width="24" height="14"/><path d="M16 28h22M16 36h22M16 44h16"/></svg>Textbooks</div>
  </div>

  <div class="abs soft-bg" role="img" aria-label="Faint background photo of people working in a print shop"></div>

  <div class="abs ghost welcome-ghost">ABOUT US</div>
  <h2 class="abs section-title welcome-title">Welcome to University</h2>
  <div class="abs welcome-text">
    <p>We are located in the campus, which has specialized in the service of school staff, as well as providing general public printing.</p>
    <p>Higher education publishes seminars and first-class textbooks for courses, prints theses for lesson, as well as working on an unprecedented number of smaller pieces for students, teachers and organizations. These include brochures, reports, questionnaires, business cards, books...</p>
  </div>
  <a class="abs btn btn-green welcome-btn">Read more
    <svg width="16" height="16" viewBox="0 0 16 16"><circle cx="8" cy="8" r="7" fill="#fff"/><path d="M6 4.5 9.5 8 6 11.5" fill="none" stroke="#0d5a2c" stroke-width="2"/></svg></a>
  <div class="abs video" role="img" aria-label="Video still of a print shop worker handing over printed work"></div>
  <div class="abs play"><svg width="66" height="46" viewBox="0 0 66 46"><path d="M26 14v18l15-9z" fill="#fff"/></svg></div>
  <div class="abs divider"></div>

  <div class="abs ghost center latest-ghost">LATEST WORK</div>
  <h2 class="abs section-title center latest-title">Latest Work</h2>
  <p class="abs lede center latest-lede">Higher education is a tailored print shop, The Heron is the official eco-label of the Nordic countries, which<br>has created a foothold in this country and is known among consumers.</p>

  <div class="abs work" style="left:102px;top:1581px">
    <div class="work-img" style="background:linear-gradient(135deg,#3a3a3a,#7a5a3c 60%,#e06a2a)" role="img" aria-label="Business card samples"></div>
    <div class="work-cap"><h3>Business Cards</h3><p>Lorem ipsum dolor sit consectetur...</p></div>
  </div>
  <div class="abs work" style="left:359px;top:1581px">
    <div class="work-img" style="background:linear-gradient(135deg,#f2f2f2,#cfd8dc 50%,#2b89a6)" role="img" aria-label="Company brochure samples"></div>
    <div class="work-cap"><h3>Brochure Printing</h3><p>Lorem ipsum dolor sit consectetur...</p></div>
  </div>
  <div class="abs work" style="left:617px;top:1581px">
    <div class="work-img" style="background:linear-gradient(180deg,#8fb4d6,#c9553d 40%,#e2b04a 70%,#4a6ea8)" role="img" aria-label="Stack of printed books"></div>
    <div class="work-cap"><h3>Book Printing</h3><p>Lorem ipsum dolor sit consectetur...</p></div>
  </div>
  <div class="abs work" style="left:874px;top:1581px">
    <div class="work-img" style="background:linear-gradient(180deg,#d7e3ea,#9fb5a0 55%,#6d6d6d)" role="img" aria-label="Street poster display"></div>
    <div class="work-cap"><h3>Posters</h3><p>Lorem ipsum dolor sit consectetur...</p></div>
  </div>
  <a class="abs btn btn-yellow works-btn">View all works
    <svg width="16" height="16" viewBox="0 0 16 16"><circle cx="8" cy="8" r="7" fill="#1f1f1f"/><path d="M6 4.5 9.5 8 6 11.5" fill="none" stroke="#e7b812" stroke-width="2"/></svg></a>

  <section class="abs how"></section>
  <div class="abs how-lower" role="img" aria-label="Faint background photo of people at work"></div>
  <div class="abs ghost center how-ghost">HOW IT WORKS</div>
  <h2 class="abs section-title center how-title">How it works</h2>
  <p class="abs lede center how-lede">Higher education is a tailored print shop, The Heron is the official eco-label of the Nordic countries, which<br>has created a foothold in this country and is known among consumers.</p>
  <svg class="abs" style="left:270px;top:2300px" width="662" height="90" viewBox="0 0 662 90">
    <path d="M0 50 C80 100 150 10 330 50 S560 0 662 50" fill="none" stroke="#e7b812" stroke-width="3" stroke-dasharray="6 5"/>
  </svg>
  <div class="abs step" style="left:168px;top:2249px">
    <svg width="80" height="70" viewBox="0 0 80 70" fill="none" stroke="#e3262b" stroke-width="2.5"><rect x="8" y="6" width="38" height="50"/><path d="M16 40v8M24 32v16M32 24v24M50 18h22M50 30h22M50 42h22"/><circle cx="28" cy="58" r="8"/><path d="M24 58l3 3 5-6"/></svg>Senda Verk</div>
  <div class="abs step" style="left:498px;top:2249px">
    <svg width="80" height="70" viewBox="0 0 80 70" fill="none" stroke="#e3262b" stroke-width="2.5"><rect x="8" y="6" width="64" height="44"/><path d="M40 50v10M26 62h28M22 40l10-22 8 14 8-10 10 18z"/></svg>Hanna Verk</div>
  <div class="abs step" style="left:829px;top:2249px">
    <svg width="80" height="70" viewBox="0 0 80 70" fill="none" stroke="#e3262b" stroke-width="2.5"><path d="M14 34h8l6 20h30l6-16H26"/><circle cx="32" cy="62" r="3"/><circle cx="54" cy="62" r="3"/><path d="M30 26l14-18 8 6-14 18zM46 28l16-16 6 6-16 16z"/></svg>FA Tilbod</div>

  <div class="abs ghost center books-ghost">OUR BOOKS</div>
  <h2 class="abs section-title center books-title">Our Books</h2>

  <div class="abs book-cover" style="left:100px;top:2633px;background:linear-gradient(160deg,#ffffff 0%,#e6e6e6 55%,#2c3e50 100%)" role="img" aria-label="Book cover with city tower and red accents"></div>
  <div class="abs book-info" style="left:290px;top:2633px">
    <h3>Book Name</h3><div class="author">Book Author Name</div>
    <p>Duis aute irure dolor in reprehenderit in voluptate velit esse cillum dolore eu fugiat nulla pariatur. Excepteur sint occaecat cupidatat...</p>
    <a class="btn btn-green buy">Buy now
      <svg width="14" height="14" viewBox="0 0 16 16"><circle cx="8" cy="8" r="7" fill="#fff"/><path d="M6 4.5 9.5 8 6 11.5" fill="none" stroke="#0d5a2c" stroke-width="2"/></svg></a>
  </div>

  <div class="abs book-cover" style="left:619px;top:2633px;background:linear-gradient(180deg,#ffffff 0%,#dceef8 40%,#1f7fbf 80%,#0f4f86 100%)" role="img" aria-label="Book cover with blue city skyline"></div>
  <div class="abs book-info" style="left:811px;top:2633px">
    <h3>Book Name</h3><div class="author">Book Author Name</div>
    <p>Duis aute irure dolor in reprehenderit in voluptate velit esse cillum dolore eu fugiat nulla pariatur. Excepteur sint occaecat cupidatat...</p>
    <a class="btn btn-green buy">Buy now
      <svg width="14" height="14" viewBox="0 0 16 16"><circle cx="8" cy="8" r="7" fill="#fff"/><path d="M6 4.5 9.5 8 6 11.5" fill="none" stroke="#0d5a2c" stroke-width="2"/></svg></a>
  </div>

  <footer>
    <div class="abs foot-photo" role="img" aria-label="Photo of glass office towers against the sky"></div>
    <div class="abs foot-mid">
      <div class="abs foot-h" style="left:0;width:400px;top:53px">Newsletter Subscription</div>
      <div class="abs email-field">Email</div>
      <a class="abs btn btn-red subscribe">Subscribe</a>
      <div class="abs foot-h" style="left:0;width:400px;top:202px">Contact us</div>
      <div class="abs contact-line" style="left:0;width:400px;top:232px">
        <svg width="14" height="14" viewBox="0 0 14 14"><path d="M3 1l3 3-2 2c1 2 2 3 4 4l2-2 3 3-2 2C6 13 1 8 1 3z" fill="#fff"/></svg>555 0192</div>
      <div class="abs contact-line" style="left:0;width:400px;top:262px">
        <svg width="16" height="12" viewBox="0 0 16 12"><rect width="16" height="12" fill="#fff"/><path d="M0 0l8 7 8-7" fill="none" stroke="#262626" stroke-width="1.5"/></svg>verk@vindurgata.is</div>
      <div class="abs" style="left:0;width:400px;top:305px;font-size:13px">© Copyright 2018 Vindurgata. All Rights Reserved.</div>
    </div>
    <div class="abs foot-map" role="img" aria-label="Street map showing the shop location">
      <a class="abs btn btn-yellow direction">
        <svg width="14" height="12" viewBox="0 0 14 12"><path d="M1 11V7c0-2 2-3 4-3h6M8 1l3 3-3 3" fill="none" stroke="#1f1f1f" stroke-width="2"/></svg>Get direction</a>
      <svg class="abs" style="left:232px;top:138px" width="24" height="32" viewBox="0 0 24 32"><path d="M12 31C4 19 2 15 2 11a10 10 0 0 1 20 0c0 4-2 8-10 20z" fill="#e3262b"/><circle cx="12" cy="11" r="4" fill="#fff"/></svg>
    </div>
    <div class="abs up">
      <svg width="22" height="22" viewBox="0 0 22 22" fill="none" stroke="#1f1f1f" stroke-width="2.5"><path d="M4 12l7-7 7 7M4 19l7-7 7 7"/></svg>
    </div>
  </footer>

</div>
</body>
</html>
```